Redesign of business card for Cedar Ridge Mechanical

We are looking for a new design for our business cards for Cedar Ridge Mechanical. We are a plumbing & HVAC construction company, operating on the West Coast of Canada and USA. Logo attached.
Industry/Entity Type
Construction - Plumbing & HVAC
Contact Information for Business Card
Name, address, phone numbers, email, website address
Look and feel
Each slider illustrates characteristics of the customer's brand and the style your logo design should communicate.

```html
<!DOCTYPE html>
<html lang="en">
<head>
<meta charset="utf-8">
<title>Cedar Ridge Mechanical – Business Card</title>
<link href="https://fonts.googleapis.com/css2?family=Montserrat:wght@400;500;700&display=swap" rel="stylesheet">
<style>
  :root {
    --page-bg: #d8d1c7;
    --card-bg: #ece7e0;
    --ink: #111111;
    --ink-soft: #1e1e1e;
    --band: #0d0d0d;
    --band-text: #e9e9e9;
  }
  * { margin: 0; padding: 0; box-sizing: border-box; }
  html, body {
    width: 1200px;
    height: 1047px;
    overflow: hidden;
    background: var(--page-bg);
    font-family: "Montserrat", Arial, sans-serif;
    color: var(--ink);
  }
  .card {
    position: absolute;
    left: 100px;
    top: 251px;
    width: 1000px;
    height: 545px;
    background: var(--card-bg);
    border-radius: 24px;
    overflow: hidden;
    box-shadow: 0 18px 40px rgba(0,0,0,0.18);
  }
  .brand {
    position: absolute;
    left: 108px;
    top: 168px;
    width: 370px;
    display: flex;
    align-items: center;
    gap: 22px;
  }
  .brand-mark {
    width: 64px;
    height: 64px;
    flex: none;
    background: var(--ink);
  }
  .brand-name {
    font-weight: 700;
    font-size: 34px;
    line-height: 1.12;
    color: var(--ink);
  }
  .divider {
    position: absolute;
    left: 516px;
    top: 133px;
    width: 3px;
    height: 278px;
    background: var(--ink);
  }
  .details {
    position: absolute;
    left: 550px;
    top: 126px;
  }
  .person-name {
    font-weight: 700;
    font-size: 42px;
    letter-spacing: 0.5px;
    line-height: 1;
    text-transform: uppercase;
  }
  .person-title {
    font-weight: 400;
    font-size: 25px;
    margin-top: 10px;
    color: var(--ink-soft);
  }
  .contact-list {
    list-style: none;
    margin-top: 22px;
  }
  .contact-list li {
    display: flex;
    align-items: center;
    gap: 9px;
    font-size: 25px;
    line-height: 34px;
    color: var(--ink-soft);
  }
  .contact-list svg { width: 22px; height: 22px; flex: none; }
  .address {
    margin-top: 16px;
    font-size: 25px;
    line-height: 34px;
    color: var(--ink-soft);
  }
  .footer-band {
    position: absolute;
    left: 0;
    bottom: 0;
    width: 1000px;
    height: 68px;
  }
  .website {
    position: absolute;
    left: 284px;
    bottom: 36px;
    width: 432px;
    text-align: center;
    font-size: 23px;
    font-weight: 500;
    color: var(--band-text);
  }
</style>
</head>
<body>
  <div class="card">
    <div class="brand">
      <div class="brand-mark"></div>
      <div class="brand-name">Cedar Ridge<br>Mechanical</div>
    </div>

    <div class="divider"></div>

    <div class="details">
      <div class="person-name">Daniel Harper</div>
      <div class="person-title">Managing Director</div>
      <ul class="contact-list">
        <li>
          <svg viewBox="0 0 24 24" aria-hidden="true"><path fill="#111" d="M6.6 10.8a15.1 15.1 0 0 0 6.6 6.6l2.2-2.2c.3-.3.7-.4 1-.2 1.1.4 2.3.6 3.6.6.6 0 1 .4 1 1V20c0 .6-.4 1-1 1C10.6 21 3 13.4 3 4c0-.6.4-1 1-1h3.5c.6 0 1 .4 1 1 0 1.3.2 2.5.6 3.6.1.3 0 .7-.2 1z"/></svg>
          <span>123 456 789</span>
        </li>
        <li>
          <svg viewBox="0 0 24 24" aria-hidden="true"><rect x="6" y="2" width="12" height="20" rx="2" fill="none" stroke="#111" stroke-width="2"/><circle cx="12" cy="18" r="1.2" fill="#111"/></svg>
          <span>123 456 0000</span>
        </li>
        <li>
          <svg viewBox="0 0 24 24" aria-hidden="true"><rect x="3" y="6" width="18" height="13" rx="1.5" fill="none" stroke="#111" stroke-width="2"/><path d="M3 7l9 6 9-6" fill="none" stroke="#111" stroke-width="2"/></svg>
          <span>info@cedarridgemech.com</span>
        </li>
      </ul>
      <div class="address">Your address, City<br>State, Zip 1234</div>
    </div>

    <svg class="footer-band" viewBox="0 0 1000 68" aria-hidden="true">
      <path fill="#0d0d0d" d="M0 35 H250 L284 0 H716 L750 35 H1000 V68 H0 Z"/>
    </svg>
    <div class="website">www.cedarridgemech.com</div>
  </div>
</body>
</html>
```